A clean crisp business card for a Landscape Construction company. Designed to be easy to read contact/ info and also be appealing/interesting, unlike a traditional business card.

Industry/Entity Type

Landscape Construction

Contact Information for Business Card

Company name : Brambleford Landscape Construction, phone number: (877) 62Vista, website:Bramblefordyards.example, Email, sales@bramblefordyards.example

Requirements
Nice to have
• Luxurious finishes/ details…. Icons or emblems next to contact info
Should not have
• Clipart or general pictures

```html
<!DOCTYPE html>
<html lang="en">
<head>
<meta charset="utf-8">
<title>Brambleford Landscape Construction – Business Card</title>
<link rel="stylesheet" href="https://fonts.googleapis.com/css2?family=Cinzel:wght@400;600&family=Arimo:wght@400&display=swap">
<style>
  :root {
    --page: #3a3a3f;
    --card: #050505;
    --card-sheen: #1a1a1c;
    --lime: #9ccc2c;
    --blue: #2a78d0;
    --white: #f2f2f2;
  }
  * { box-sizing: border-box; margin: 0; padding: 0; }
  html, body { width: 1200px; height: 913px; overflow: hidden; }
  body {
    background: var(--page);
    position: relative;
    font-family: "Arimo", Arial, sans-serif;
  }
  .card {
    position: absolute;
    width: 620px;
    height: 354px;
    border-radius: 14px;
    background: linear-gradient(135deg, var(--card-sheen) 0%, var(--card) 35%, var(--card) 100%);
    border: 2px solid var(--lime);
    box-shadow: 0 18px 40px rgba(0,0,0,.45);
    overflow: hidden;
  }
  .card--front { left: 60px; top: 60px; }
  .card--back { left: 520px; top: 490px; }

  .brand {
    position: absolute;
    display: flex;
    align-items: center;
    gap: 14px;
  }
  .brand__dot {
    flex: none;
    width: 18px; height: 18px;
    border-radius: 50%;
    background: var(--lime);
  }
  .brand__name {
    font-family: "Cinzel", Georgia, serif;
    font-weight: 600;
    color: var(--blue);
    text-transform: uppercase;
    line-height: 1.15;
    letter-spacing: .04em;
  }
  .card--front .brand { left: 36px; top: 130px; width: 260px; }
  .card--front .brand__name { font-size: 22px; }
  .card--back .brand { left: 90px; top: 130px; width: 460px; justify-content: center; }
  .card--back .brand__name { font-size: 32px; text-align: center; }

  .divider {
    position: absolute;
    left: 318px; top: 70px;
    width: 1px; height: 170px;
    background: var(--lime);
  }
  .contact {
    position: absolute;
    left: 344px; top: 70px;
    right: 20px;
  }
  .contact__name {
    font-family: "Cinzel", Georgia, serif;
    font-weight: 400;
    font-size: 27px;
    color: var(--blue);
    text-transform: uppercase;
    line-height: 1.1;
  }
  .contact__role {
    font-family: "Cinzel", Georgia, serif;
    font-size: 15px;
    color: var(--lime);
    text-transform: uppercase;
    margin-top: 4px;
    margin-bottom: 20px;
  }
  .contact__list { list-style: none; }
  .contact__item {
    display: flex;
    align-items: center;
    gap: 8px;
    color: var(--white);
    font-size: 13px;
    line-height: 1.9;
  }
  .contact__icon { width: 12px; height: 12px; flex: none; }
</style>
</head>
<body>
  <section class="card card--front" aria-label="Business card front">
    <div class="brand">
      <span class="brand__dot"></span>
      <span class="brand__name">Brambleford Landscape Construction</span>
    </div>
    <div class="divider"></div>
    <div class="contact">
      <h1 class="contact__name">Daniel Harlow</h1>
      <p class="contact__role">Director</p>
      <ul class="contact__list">
        <li class="contact__item">
          <svg class="contact__icon" viewBox="0 0 12 12"><path d="M2.5 1 L4.5 1 L5 3.5 L3.8 4.5 Q5 7 7.5 8.2 L8.5 7 L11 7.5 L11 9.5 Q10 11 8 10.5 Q2.5 8.5 1 3.5 Q1 1.8 2.5 1 Z" fill="var(--lime)"/></svg>
          (877) 62Vista
        </li>
        <li class="contact__item">
          <svg class="contact__icon" viewBox="0 0 12 12"><rect x="1" y="2.5" width="10" height="7" fill="none" stroke="var(--lime)" stroke-width="1.2"/><path d="M1 2.5 L6 6.5 L11 2.5" fill="none" stroke="var(--lime)" stroke-width="1.2"/></svg>
          sales@bramblefordyards.example
        </li>
        <li class="contact__item">
          <svg class="contact__icon" viewBox="0 0 12 12"><circle cx="6" cy="6" r="5" fill="none" stroke="var(--lime)" stroke-width="1.1"/><ellipse cx="6" cy="6" rx="2.2" ry="5" fill="none" stroke="var(--lime)" stroke-width="1"/><path d="M1 6 H11" stroke="var(--lime)" stroke-width="1"/></svg>
          www.bramblefordyards.example
        </li>
      </ul>
    </div>
  </section>

  <section class="card card--back" aria-label="Business card back">
    <div class="brand">
      <span class="brand__dot"></span>
      <span class="brand__name">Brambleford Landscape Construction</span>
    </div>
  </section>
</body>
</html>
```